Delegate visit agenda

We need a creative, yet simple and official design for an agenda to be handed out for delegates visiting our organization. The design needs to be creative, informative and visual when possible. Flat design is desired but other options are welcomed. The agenda should be 3 pages in lengths only. Page 1 should have the company logo with an event title (with the ability to add country flag) and the dates of the event. Pages 2 should include photos of receiving delegate (e.g. VIPs) and any other relevant people. Page 3 should include agenda entries with the following information: title of entry, date and time, location, relevant pictures (e.g. a hotel or flight). The generic style of an infographic.
Updates
Project Deadline Extended
Reason: Not enough submissions received.
No optimal design (i.e. creative and attractive) received.

Brief has been updated with samples.

Target Market(s)
Very high profile people (e.g. presidents, ministers, GM,...etc.)
Industry/Entity Type
Hotel
Colors
Designer to choose colors to be used in the design.
Look and feel
Each slider illustrates characteristics of the customer's brand and the style your logo design should communicate.

```html
<!DOCTYPE html>
<html lang="en">
<head>
<meta charset="utf-8">
<title>Delegate Visit Agenda</title>
<link rel="stylesheet" href="https://fonts.googleapis.com/css2?family=Source+Sans+3:wght@400;600;700&display=swap">
<style>
  :root {
    --gold: #c38a33;
    --gold-light: #d9aa5e;
    --ink: #2b2b2b;
    --body-ink: #3a3a3a;
    --white: #ffffff;
    --flag-green: #8fb394;
    --flag-red: #cf7d70;
    --flag-gold: #e4c27a;
  }
  html, body {
    margin: 0;
    padding: 0;
    width: 1200px;
    height: 849px;
    overflow: hidden;
  }
  .page {
    position: relative;
    width: 1200px;
    height: 849px;
    overflow: hidden;
    font-family: "Source Sans 3", sans-serif;
    color: var(--body-ink);
  }
  .backdrop {
    position: absolute;
    inset: 0;
    background:
      radial-gradient(ellipse at 85% 25%, #dccab4 0%, rgba(220,202,180,0) 45%),
      radial-gradient(ellipse at 30% 80%, #ddd2c6 0%, rgba(221,210,198,0) 50%),
      linear-gradient(100deg, #c6c6da 0%, #d6d4e2 40%, #e2d6c8 75%, #eadccb 100%);
  }
  .orbit {
    position: absolute;
    inset: 0;
  }
  .portrait {
    position: absolute;
    width: 166px;
    height: 166px;
    border-radius: 50%;
    background: var(--white);
    border: 4px solid var(--gold);
    box-sizing: border-box;
  }
  .flags {
    position: absolute;
    left: 427px;
    top: 437px;
    width: 300px;
    height: 136px;
    border-radius: 50%;
    transform: rotate(12deg);
    background: linear-gradient(120deg, var(--flag-green) 0%, var(--flag-red) 55%, var(--flag-gold) 100%);
    opacity: 0.85;
  }
  .entry {
    position: absolute;
    font-size: 11.2px;
    line-height: 15.4px;
  }
  .entry h2 {
    margin: 0;
    font-size: 13.5px;
    font-weight: 700;
    color: var(--ink);
    line-height: 16px;
  }
  .entry h3 {
    margin: 0 0 5px;
    font-size: 10.4px;
    font-weight: 400;
    color: var(--ink);
    line-height: 15px;
  }
  .entry p {
    margin: 0;
    text-align: justify;
    text-align-last: left;
  }
  .entry.right-aligned { text-align: right; }
  .entry.right-aligned p { text-align-last: right; }
</style>
</head>
<body>
<main class="page">
  <div class="backdrop" role="img" aria-label="Soft blurred photograph of a city skyline with hotel towers"></div>

  <svg class="orbit" width="1200" height="849" viewBox="0 0 1200 849" aria-hidden="true">
    <g transform="translate(597 423) rotate(31.4)" fill="none">
      <ellipse rx="528" ry="265" stroke="var(--gold)" stroke-width="4"/>
      <ellipse rx="540" ry="276" stroke="var(--gold-light)" stroke-width="1"/>
      <ellipse rx="520" ry="256" stroke="var(--gold-light)" stroke-width="1"/>
      <ellipse rx="548" ry="284" stroke="var(--gold-light)" stroke-width="0.8" opacity="0.8"/>
    </g>
  </svg>

  <div class="flags" role="img" aria-label="Illustration of the host and visiting countries' national flags waving side by side"></div>

  <svg class="orbit" width="1200" height="849" viewBox="0 0 1200 849" aria-hidden="true">
    <g transform="translate(577 505) rotate(12)" fill="none">
      <ellipse rx="168" ry="80" stroke="var(--gold)" stroke-width="2"/>
      <ellipse rx="162" ry="74" stroke="var(--gold-light)" stroke-width="1"/>
    </g>
  </svg>

  <div class="portrait" style="left:67px; top:67px;" role="img" aria-label="Photo of receiving delegate"></div>
  <div class="portrait" style="left:106px; top:265px;" role="img" aria-label="Photo of receiving delegate"></div>
  <div class="portrait" style="left:207px; top:457px;" role="img" aria-label="Photo of receiving delegate"></div>
  <div class="portrait" style="left:391px; top:578px;" role="img" aria-label="Photo of receiving delegate"></div>
  <div class="portrait" style="left:638px; top:105px;" role="img" aria-label="Photo of receiving delegate"></div>
  <div class="portrait" style="left:820px; top:222px;" role="img" aria-label="Photo of receiving delegate"></div>
  <div class="portrait" style="left:921px; top:414px;" role="img" aria-label="Photo of receiving delegate"></div>
  <div class="portrait" style="left:961px; top:614px;" role="img" aria-label="Photo of receiving delegate"></div>

  <section class="entry" style="left:247px; top:131px; width:326px;">
    <h2>Lorem ipsum</h2>
    <h3>LOREM IPSUM</h3>
    <p>Lorem ipsum dolor sit amet, error regione voluptua mea ei, ei ullum civibus efficiantur pri. Ei exerci reprimique has. Duo te dicant complectitur, pri ei &nbsp;&nbsp;nihil munere doctus. Vix id exerci verear, mea ea accusata petentium ullamcorper. Vel offendit percipit maluisset ea.</p>
  </section>

  <section class="entry" style="left:283px; top:289px; width:290px;">
    <h2>Lorem ipsum</h2>
    <h3>LOREM IPSUM</h3>
    <p>Lorem ipsum dolor sit amet, error regione voluptua mea ei, ei ullum civibus efficiantur pri. Ei exerci reprimique has. Duo te dicant complectitur, pri ei &nbsp;&nbsp;nihil munere doctus. Vix id exerci verear, mea ea accusata petentium ullamcorper. Vel offendit percipit maluisset ea.</p>
  </section>

  <section class="entry right-aligned" style="left:24px; top:467px; width:179px;">
    <h2>Lorem ipsum</h2>
    <h3>LOREM IPSUM</h3>
    <p>Lorem ipsum dolor sit amet, error regione voluptua mea ei, ei ullum civibus efficiantur pri. Ei exerci reprimique has. Duo te dicant complectitur, pri ei &nbsp;&nbsp;nihil munere doctus. Vix id exerci verear, mea ea accusata petentium ullamcorper. Vel offendit percipit maluisset ea.</p>
  </section>

  <section class="entry right-aligned" style="left:37px; top:661px; width:348px;">
    <h2>Lorem ipsum</h2>
    <h3>LOREM IPSUM</h3>
    <p style="margin-top:10px;">Lorem ipsum dolor sit amet, error regione voluptua mea ei, ei ullum civibus efficiantur pri. Ei exerci reprimique has. Duo te dicant complectitur, pri ei &nbsp;&nbsp;nihil munere doctus. Vix id exerci verear, mea ea accusata petentium ullamcorper. Vel offendit percipit maluisset ea.</p>
  </section>

  <section class="entry" style="left:815px; top:114px; width:220px;">
    <h2>Lorem ipsum</h2>
    <h3>LOREM IPSUM</h3>
    <p>Lorem ipsum dolor sit amet, error regione voluptua mea ei, ei ullum civibus efficiantur pri. Ei exerci reprimique has. Duo te dicant</p>
  </section>

  <section class="entry" style="left:998px; top:233px; width:170px;">
    <h2>Lorem ipsum</h2>
    <h3>LOREM IPSUM</h3>
    <p>Lorem ipsum dolor sit amet, error regione voluptua mea ei, ei ullum civibus efficiantur pri. Ei exerci reprimique has. Duo te dicant complectitur, pri ei &nbsp;&nbsp;nihil munere</p>
  </section>

  <section class="entry right-aligned" style="left:750px; top:426px; width:167px;">
    <h2>Lorem ipsum</h2>
    <h3>LOREM IPSUM</h3>
    <p>Lorem ipsum dolor sit amet, error regione voluptua mea ei, ei ullum civibus efficiantur pri. Ei exerci reprimique has. Duo te dicant complectitur, pri ei &nbsp;&nbsp;nihil munere doctus. Vix id exerci verear, mea ea</p>
  </section>

  <section class="entry right-aligned" style="left:785px; top:613px; width:168px;">
    <h2>Lorem ipsum</h2>
    <h3>LOREM IPSUM</h3>
    <p>Lorem ipsum dolor sit amet, error regione voluptua mea ei, ei ullum civibus efficiantur pri. Ei exerci reprimique has. Duo te dicant</p>
  </section>
</main>
</body>
</html>
```